Corvane Holdings , new business card design

investment firm with corporate clients . need double sided business card , vertical and horizontal options ,logo must be clear. prefer pantone colors only and sharp design. website also www.corvane.ae

Khalid Bin Tarrafi
Managing Director
Tel. +971 4 387 2940
Mobile +971 50 518 2403
khalid@corvane.ae
Q-Span Plaza, officw 18-B07, Warqa Gardens, Dubai

Contact Information for Business Card

Khalid Bin Tarrafi
Managing Director

Font styles to use
Serif

Colors

Designer to choose colors to be used in the design.

```html
<!DOCTYPE html>
<html lang="en">
<head>
<meta charset="utf-8">
<title>Corvane Holdings – Business Card</title>
<link rel="stylesheet" href="https://fonts.googleapis.com/css2?family=Open+Sans:wght@300;400;600;700&display=swap">
<style>
  :root {
    --slate: #46455c;
    --steel: #4a7aa6;
    --stone: #cdc8c4;
    --paper: #ffffff;
    --ink: #3d3d48;
    --backdrop: #e6e3e0;
  }
  * { margin: 0; padding: 0; box-sizing: border-box; }
  html, body {
    width: 1200px; height: 997px; overflow: hidden;
    background: var(--backdrop);
    font-family: "Open Sans", Arial, sans-serif;
  }
  .canvas { position: relative; width: 1200px; height: 997px; }
  .card {
    position: absolute; width: 560px; height: 320px; overflow: hidden;
    box-shadow: 0 10px 28px rgba(0,0,0,.14);
  }
  .card-front { left: 90px; top: 110px; background: var(--paper); }
  .card-back { left: 550px; top: 560px; background: var(--slate); }

  .front-shape { position: absolute; inset: 0; }

  .brand {
    display: flex; align-items: center; gap: 9px;
    font-weight: 300; text-transform: uppercase; white-space: nowrap;
  }
  .brand-mark { width: 9px; height: 9px; background: currentColor; flex: none; }
  .card-front .brand {
    position: absolute; left: 30px; top: 64px;
    font-size: 18px; letter-spacing: 3px; line-height: 24px; color: var(--slate);
  }
  .card-back .brand {
    position: absolute; left: 0; right: 0; top: 146px;
    justify-content: center; font-size: 24px; letter-spacing: 4px; color: var(--paper);
  }

  .holder-name {
    position: absolute; left: 318px; top: 100px;
    font-size: 15px; line-height: 22px; font-weight: 700; color: var(--paper);
  }
  .holder-title {
    position: absolute; right: 22px; top: 128px;
    font-size: 11px; line-height: 16px; color: var(--paper);
  }

  .address {
    position: absolute; left: 130px; top: 196px;
    font-size: 12px; line-height: 16px; color: var(--ink);
  }
  .contacts {
    position: absolute; left: 130px; top: 240px; list-style: none;
    font-size: 12px; line-height: 16px; color: var(--ink);
  }
  .contacts li { display: flex; align-items: center; gap: 7px; }
  .contacts svg { width: 10px; height: 10px; fill: var(--slate); }
</style>
</head>
<body>
<main class="canvas">
  <section class="card card-front" aria-label="Business card front">
    <svg class="front-shape" viewBox="0 0 560 320" aria-hidden="true">
      <polygon points="240,0 560,0 560,160 470,160" fill="var(--slate)"/>
      <polygon points="310,124 560,124 560,150 300,150" fill="var(--stone)"/>
      <polygon points="318,98 560,98 560,124 308,124" fill="var(--slate)"/>
    </svg>
    <div class="brand"><span class="brand-mark"></span>Corvane Holdings</div>
    <p class="holder-name">Khalid Bin Tarrafi</p>
    <p class="holder-title">Managing Director</p>
    <p class="address">Q-Span Plaza, officw 18-B07,<br>Warqa Gardens, Dubai</p>
    <ul class="contacts">
      <li><svg viewBox="0 0 10 10"><path d="M2 0l2 2-1 1.5c.8 1.5 2 2.7 3.5 3.5L8 6l2 2-1.5 2C4 10 0 6 0 1.5z"/></svg>+971 4 387 2940</li>
      <li><svg viewBox="0 0 10 10"><path d="M2.5 0h5v10h-5zM3.5 1v7h3V1z"/></svg>+971 50 518 2403</li>
      <li><svg viewBox="0 0 10 10"><path d="M0 2h10v6H0zM0 2l5 3.5L10 2v1L5 6.5 0 3z"/></svg>khalid@corvane.ae</li>
    </ul>
  </section>

  <section class="card card-back" aria-label="Business card back">
    <div class="brand"><span class="brand-mark"></span>Corvane Holdings</div>
  </section>
</main>
</body>
</html>
```